Business Card for Industrial Distributor

We need a business card design for an industrial distributor. We sell machine parts for the manufacturing and oil industry. We would like the cards to look clean and modern but with a touch of industry.

Our colors are blue/white.

Please feel free to visit our website www.korvelpartsco.com

Target Market(s)

mexican manufacturers in the automobile/aerospace industry

Industry/Entity Type

Industrial

Colors
ffffff
0555a3

```html
<!DOCTYPE html>
<html lang="en">
<head>
<meta charset="utf-8">
<title>Korvel Business Card</title>
<link href="https://fonts.googleapis.com/css2?family=Montserrat:wght@400;500;700;800&display=swap" rel="stylesheet">
<style>
  :root {
    --page-bg: #2f3033;
    --card-white: #ffffff;
    --brand-navy: #2a3893;
    --brand-blue: #1f63c6;
    --accent-sky: #2f8fd8;
    --text-on-navy: #ffffff;
  }
  * { box-sizing: border-box; margin: 0; padding: 0; }
  html, body {
    width: 1200px; height: 900px; overflow: hidden;
    background: var(--page-bg);
    font-family: "Montserrat", sans-serif;
  }
  .stage { position: relative; width: 1200px; height: 900px; }
  .card {
    position: absolute;
    width: 560px; height: 320px;
    border-radius: 22px;
    background: var(--card-white);
    overflow: hidden;
    box-shadow: 0 18px 40px rgba(0,0,0,.45);
  }
  .card-front { left: 220px; top: 90px; }
  .card-back { left: 420px; top: 480px; }

  /* front */
  .front-brand {
    position: absolute; left: 70px; top: 115px;
    display: flex; align-items: center; gap: 18px;
  }
  .brand-dot {
    width: 78px; height: 78px; border-radius: 50%;
    background: var(--brand-blue);
  }
  .front-wordmark {
    font-weight: 800; font-size: 84px; line-height: 1;
    color: var(--brand-navy); letter-spacing: -1px;
  }
  .front-web {
    position: absolute; left: 0; right: 0; bottom: 42px;
    text-align: center; font-size: 17px; color: var(--brand-navy);
  }
  .front-web b { font-weight: 700; }

  /* back */
  .navy-band {
    position: absolute; inset: 0;
    background: var(--brand-navy);
    clip-path: polygon(0 68%, 100% 42%, 100% 100%, 0 100%);
  }
  .back-wordmark {
    position: absolute; left: 26px; top: 14px;
    font-weight: 800; font-size: 100px; line-height: 1;
    color: var(--brand-navy); letter-spacing: -2px;
  }
  .band-circle {
    position: absolute; right: 26px; top: 60px;
    width: 130px; height: 130px; border-radius: 50%;
    background: var(--brand-blue);
    border: 4px solid var(--card-white);
  }
  .person {
    position: absolute; left: 34px; top: 130px;
  }
  .person-name { font-weight: 700; font-size: 22px; line-height: 1.2; color: var(--brand-navy); }
  .person-title { font-size: 13px; color: var(--accent-sky); margin-top: 2px; }
  .contact {
    position: absolute; left: 48px; top: 226px;
    color: var(--text-on-navy); font-size: 12px; line-height: 1.4;
  }
  .contact-address { margin-bottom: 3px; }
  .contact-line { display: flex; align-items: center; gap: 9px; }
  .contact-line svg { width: 11px; height: 11px; flex: none; }
  .contact-line b { font-weight: 700; }
</style>
</head>
<body>
<main class="stage">

  <section class="card card-front" aria-label="Card front">
    <div class="front-brand">
      <span class="brand-dot"></span>
      <span class="front-wordmark">Korvel</span>
    </div>
    <p class="front-web">www.<b>korvelpartsco</b>.com</p>
  </section>

  <section class="card card-back" aria-label="Card back">
    <div class="navy-band"></div>
    <div class="back-wordmark">Korvel</div>
    <span class="band-circle"></span>
    <div class="person">
      <p class="person-name">Marcus Hale</p>
      <p class="person-title">Director</p>
    </div>
    <div class="contact">
      <p class="contact-address">P.O. Box 4821<br>Lansing, MI 48906</p>
      <p class="contact-line">
        <svg viewBox="0 0 24 24" fill="#fff"><path d="M6.6 10.8a15 15 0 0 0 6.6 6.6l2.2-2.2c.3-.3.7-.4 1-.2 1.1.4 2.3.6 3.6.6.6 0 1 .4 1 1V20c0 .6-.4 1-1 1A17 17 0 0 1 3 4c0-.6.4-1 1-1h3.5c.6 0 1 .4 1 1 0 1.3.2 2.5.6 3.6.1.3 0 .7-.2 1z"/></svg>
        <span>+330 5812-3094</span>
      </p>
      <p class="contact-line">
        <svg viewBox="0 0 24 24" fill="none" stroke="#fff" stroke-width="2.4"><rect x="2" y="5" width="20" height="14" rx="1"/><path d="M2 6l10 7 10-7"/></svg>
        <span>info@korvelpartsco.com</span>
      </p>
      <p class="contact-line">
        <svg viewBox="0 0 24 24" fill="none" stroke="#fff" stroke-width="2.2"><circle cx="12" cy="12" r="10"/><path d="M2 12h20M12 2c3 3 3 17 0 20M12 2c-3 3-3 17 0 20"/></svg>
        <span>www.<b>korvelpartsco</b>.com</span>
      </p>
    </div>
  </section>

</main>
</body>
</html>
```